Velmora Systems Website

Website design for our company: Velmora Systems.
The website should look fresh and IT focused. Please have a look at http://www.velmorasystems.example.au/ for our current design. We want something fresh and new, professional looking, in WordPress so we can easily make changes.

It Company

```html
<!DOCTYPE html>
<html lang="en">
<head>
<meta charset="utf-8">
<title>Velmora Systems</title>
<link rel="stylesheet" href="https://fonts.googleapis.com/css2?family=Open+Sans:wght@400;600;700&family=Arimo:ital,wght@0,400;0,700;1,400&display=swap">
<style>
:root{
  --green:#00b15a;
  --green-dark:#00954b;
  --blue:#0a6cc4;
  --blue-title:#0b62b0;
  --navy:#0c4a78;
  --navy-box:#17598a;
  --hero-bg:#0d1c2c;
  --text:#333;
  --muted:#777;
  --line:#c9c9c9;
}
*{box-sizing:border-box;margin:0;padding:0}
html,body{width:980px;height:1200px;overflow:hidden}
body{position:relative;font-family:"Arimo",Arial,sans-serif;color:var(--text);background:#fff}
.abs{position:absolute}
/* header */
.site-header{left:0;top:0;width:980px;height:95px;border-top:2px solid var(--blue);background:linear-gradient(#fff,#eef0f1)}
.brand{left:145px;top:17px;height:62px;width:123px;background:var(--green);border:2px solid #fff;box-shadow:0 0 0 1px #bbb;display:flex;align-items:center;justify-content:center;gap:6px;color:#fff;font-family:"Open Sans",sans-serif;font-weight:700;font-size:13px}
.brand i{width:10px;height:10px;background:#fff;display:block}
.search{left:535px;top:22px;width:152px;height:23px;border:1px solid #ccc;background:#fff;font:italic 10px "Arimo",sans-serif;color:#888;padding:5px 7px}
.search svg{position:absolute;right:6px;top:5px}
.call{left:708px;top:19px;display:flex;gap:6px;align-items:center;font-family:"Open Sans",sans-serif}
.call small{display:block;font-size:10px;color:#333}
.call strong{display:block;font-size:16px;font-weight:400;color:#222;line-height:1}
.main-nav{left:322px;top:64px;display:flex;align-items:center;font-family:"Open Sans",sans-serif;font-size:11.5px;color:#333}
.main-nav span{padding:0 12px;border-left:1px solid #bbb;line-height:14px}
.main-nav span:nth-child(2){border-left:0}
.main-nav .active{background:var(--green);color:#fff;font-weight:700;padding:3px 9px;border:0;line-height:14px}
/* hero */
.hero{left:0;top:95px;width:980px;height:343px;background:var(--hero-bg)}
.hero-photo{left:145px;top:0;width:691px;height:343px;background:linear-gradient(100deg,#8c969e 0%,#c9d0d5 35%,#f0f2f3 55%,#3b4550 80%,#222b33 100%)}
.hero-arrow{top:147px;width:30px;height:30px;border-radius:50%;background:#111;display:flex;align-items:center;justify-content:center}
.hero-caption{left:0;top:306px;width:980px;height:37px;background:rgba(10,108,196,.88);color:#fff;font-family:"Open Sans",sans-serif;font-size:19.5px;padding-left:174px;line-height:37px}
/* services */
.services{left:0;top:438px;width:980px;height:230px;background:var(--green)}
.section-head{position:absolute;left:145px;width:691px;border-bottom:1px solid rgba(255,255,255,.6);font-family:"Open Sans",sans-serif;font-weight:600;font-size:16.5px;color:#fff;padding:0 2px 5px}
.pager{position:absolute;right:2px;top:5px;display:flex;gap:10px}
.service-list{left:145px;top:72px;display:flex;gap:11.5px}
.service{width:129px;height:130px;background:var(--blue);border-radius:3px;text-align:center;color:#fff;font-family:"Open Sans",sans-serif;font-weight:600;font-size:11px}
.service .disc{width:102px;height:78px;margin:14px auto 12px;border-radius:50%;background:#fff;box-shadow:0 3px 4px rgba(0,0,0,.25);display:flex;align-items:center;justify-content:center}
.fold{left:130px;top:668px;width:720px;height:18px;background:radial-gradient(ellipse at top,rgba(0,0,0,.35),transparent 70%)}
/* content columns */
.col-title{font-family:"Open Sans",sans-serif;font-weight:600;font-size:17px;color:var(--blue-title);border-bottom:1px solid var(--line);padding-bottom:3px;margin-bottom:9px}
.about{left:145px;top:711px;width:209px}
.about .photo{height:96px;background:linear-gradient(90deg,#b8c2cb,#e6e1da 50%,#4d5966);margin-bottom:8px}
.about p{font-size:8.6px;line-height:13px;text-align:justify;color:#444}
.more{display:block;text-align:right;color:var(--green-dark);font-weight:700;font-size:8.6px;margin-top:6px}
.testimonials{left:384px;top:711px;width:209px}
.quote{font-size:8.6px;line-height:15px;color:#444;margin-bottom:5px}
.quote b{font-family:Georgia,serif;color:#aaa;font-size:13px}
.cite{text-align:right;font-weight:700;font-size:8.4px;line-height:11px;color:#333;margin-bottom:7px}
.quick{left:626px;top:711px;width:210px}
.field{height:22px;border:1px solid #c8c8c8;border-radius:2px;font:italic 8.6px "Arimo",sans-serif;color:#777;padding:5px 8px;margin-bottom:11px;box-shadow:inset 0 1px 2px rgba(0,0,0,.08)}
.field.tall{height:62px}
.btn{display:inline-block;background:var(--green);color:#fff;font-family:"Open Sans",sans-serif;font-size:11px;padding:3px 10px;border-radius:1px}
/* clients */
.clients{left:145px;top:972px;width:435px}
.client-row{display:flex;justify-content:space-between;align-items:center;padding:8px 0 0;font-family:"Open Sans",sans-serif;font-weight:700;font-size:16px;color:#444}
.client-row span{display:flex;gap:5px;align-items:center}
.client-row i{width:12px;height:12px;background:#777;display:block}
.remote{left:621px;top:972px;width:210px}
/* footer */
.site-footer{left:0;top:1079px;width:980px;height:121px;background:var(--navy);border-top:3px solid #ddd;color:#fff}
.f-box{position:absolute;top:16px;height:59px;background:var(--navy-box);border:1px solid #2a6b9c;padding:7px 9px;font-family:"Open Sans",sans-serif;font-size:11px;font-weight:600}
.f-box small{display:flex;align-items:center;gap:6px;font:9px "Arimo",sans-serif;margin-top:4px}
.email-in{display:flex;margin-top:6px;gap:5px}
.email-in div{width:139px;height:21px;background:#134f7d;font:italic 9px "Arimo",sans-serif;padding:6px 7px}
.email-in b{width:24px;height:21px;background:#0e3f66;display:flex;align-items:center;justify-content:center}
.social{display:flex;gap:9px;margin-top:8px}
.social i{width:19px;height:19px;display:block;border-radius:2px}
.f-brand{left:712px;top:15px;width:123px;height:62px;background:var(--green);border:2px solid #fff;display:flex;align-items:center;justify-content:center;gap:6px;font-family:"Open Sans",sans-serif;font-weight:700;font-size:13px}
.f-brand i{width:10px;height:10px;background:#fff;display:block}
.f-links{left:145px;top:97px;font-size:8.6px}
.f-links .on{color:var(--green)}
.copy{left:628px;top:97px;font-size:8.6px}
</style>
</head>
<body>

<header class="site-header abs">
  <div class="brand abs"><i></i>Velmora Systems</div>
  <div class="search abs">search
    <svg width="11" height="11" viewBox="0 0 11 11"><circle cx="4.5" cy="4.5" r="3.5" fill="none" stroke="#888" stroke-width="1.4"/><path d="M7 7l3 3" stroke="#888" stroke-width="1.5"/></svg>
  </div>
  <div class="call abs">
    <svg width="24" height="24" viewBox="0 0 24 24"><circle cx="12" cy="12" r="11" fill="none" stroke="#00b15a" stroke-width="1.6"/><path d="M9 6c-2 1-2 4 0 8s5 5 6 4l1-2-2-1-1 1c-1 0-3-3-3-4l1-1-1-2z" fill="#00b15a"/></svg>
    <div><small>Call Us Today</small><strong>123 555 0190</strong></div>
  </div>
  <nav class="main-nav abs">
    <span class="active">HOME</span><span>ABOUT US</span><span>SERVICES</span><span>SUPPORT</span><span>TESTIMONIALS</span><span>CLIENTS</span><span>CONTACT US</span>
  </nav>
</header>

<section class="hero abs">
  <div class="hero-photo abs" role="img" aria-label="Engineer working on a laptop beside server racks in a data centre"></div>
  <div class="hero-arrow abs" style="left:147px"><svg width="10" height="14"><path d="M7 2L2 7l5 5" fill="none" stroke="#fff" stroke-width="1.5"/></svg></div>
  <div class="hero-arrow abs" style="left:803px"><svg width="10" height="14"><path d="M3 2l5 5-5 5" fill="none" stroke="#fff" stroke-width="1.5"/></svg></div>
  <div class="hero-caption abs">WE HAVE SPECIALISED ENGINEERS, TRAINED TO DO SPECIALISED WORK</div>
</section>

<section class="services abs">
  <h2 class="section-head" style="top:26px">Our Services
    <span class="pager"><svg width="8" height="12"><path d="M6 1L1 6l5 5" fill="none" stroke="#fff" stroke-width="1.3"/></svg><svg width="8" height="12"><path d="M2 1l5 5-5 5" fill="none" stroke="#fff" stroke-width="1.3"/></svg></span>
  </h2>
  <div class="service-list abs">
    <div class="service"><div class="disc"><svg width="50" height="40" viewBox="0 0 50 40"><path d="M12 34L32 10M18 34L38 10" stroke="#00b15a" stroke-width="5"/><rect x="28" y="4" width="14" height="8" fill="#00b15a"/><rect x="10" y="4" width="8" height="8" fill="#00b15a" transform="rotate(40 14 8)"/></svg></div>ON-SITE SERVICE</div>
    <div class="service"><div class="disc"><svg width="56" height="44" viewBox="0 0 56 44"><rect x="8" y="6" width="32" height="22" fill="none" stroke="#555" stroke-width="3"/><path d="M18 34h12" stroke="#555" stroke-width="3"/><circle cx="40" cy="30" r="10" fill="#fff" stroke="#555" stroke-width="3"/><path d="M36 28l4-3M44 32l-4 3" stroke="#555" stroke-width="2"/></svg></div>REMOTE DESKTOP</div>
    <div class="service"><div class="disc"><svg width="56" height="44" viewBox="0 0 56 44"><path d="M10 6v12c0 8 12 8 12 0V6" fill="none" stroke="#555" stroke-width="3"/><path d="M16 26v6c0 8 16 8 16 0v-6" fill="none" stroke="#555" stroke-width="3"/><circle cx="32" cy="23" r="4" fill="none" stroke="#555" stroke-width="2.5"/><circle cx="44" cy="12" r="5" fill="none" stroke="#555" stroke-width="3" stroke-dasharray="3 2"/></svg></div>MEDICAL IT SERVICE</div>
    <div class="service"><div class="disc"><svg width="56" height="44" viewBox="0 0 56 44"><rect x="8" y="6" width="34" height="24" fill="none" stroke="#555" stroke-width="3"/><path d="M12 24l8-8 6 5 10-9" fill="none" stroke="#555" stroke-width="2"/><circle cx="40" cy="28" r="7" fill="#fff" stroke="#555" stroke-width="3"/><path d="M45 33l6 6" stroke="#555" stroke-width="4"/></svg></div>PHARMACY IT SERVICE</div>
    <div class="service"><div class="disc"><svg width="56" height="44" viewBox="0 0 56 44"><rect x="8" y="8" width="38" height="24" fill="none" stroke="#555" stroke-width="3"/><path d="M22 38h12M28 32v6" stroke="#555" stroke-width="3"/><path d="M22 26l4-1 12-14-3-3-12 14z" fill="#555"/></svg></div>WEBSITE DESIGN</div>
  </div>
</section>
<div class="fold abs"></div>

<section class="about abs">
  <h2 class="col-title">About Velmora Systems</h2>
  <div class="photo" role="img" aria-label="Team of colleagues talking around a meeting table"></div>
  <p>Velmora Systems is a Harborview based company with a single objective - to excel in the support and service of all computer and IT needs. We provide a high level of consulting services using the most experienced engineers at a reasonable and fair price. We believe in using a Business Value approach to every</p>
  <span class="more">Read More »</span>
</section>

<section class="testimonials abs">
  <h2 class="col-title">Client Testimonials</h2>
  <p class="quote"><b>“</b> Nonummy nibh uismod tincidunt ut laoreet dolore magna aliquam erat volutpat. Ut wisi enim ad minim nonummy nibh euismod tincidunt <b>”</b></p>
  <p class="cite">Darren Kell - Northgate Dental</p>
  <p class="quote"><b>“</b> I have always found the team extremely helpful with their advice over the phone. They also have the ability to access our computers remotely, and can rectify most problems quite swiftly. I have no hesitation in recommending Velmora Systems for all of your IT needs.<b>”</b></p>
  <p class="cite">Marcus Pelloni B.Pharm<br>Westbrook Community Pharmacy, Elm Ridge</p>
  <span class="more">Read More »</span>
</section>

<section class="quick abs">
  <h2 class="col-title">Quick Contact</h2>
  <div class="field">Name</div>
  <div class="field">Email</div>
  <div class="field">Phone</div>
  <div class="field tall">Message</div>
  <span class="btn">Submit</span>
</section>

<section class="clients abs">
  <h2 class="col-title" style="position:relative">Our Clients
    <span class="pager" style="top:6px"><svg width="8" height="12"><path d="M6 1L1 6l5 5" fill="none" stroke="#0a6cc4" stroke-width="1.3"/></svg><svg width="8" height="12"><path d="M2 1l5 5-5 5" fill="none" stroke="#00b15a" stroke-width="1.3"/></svg></span>
  </h2>
  <div class="client-row">
    <span><i></i>Quorvex</span><span><i></i>Stratanet</span><span>Halden</span><span>Brevix</span>
  </div>
</section>

<section class="remote abs">
  <h2 class="col-title">Remote Support</h2>
  <div class="field" style="margin-top:4px">Enter your 6 digit code</div>
  <span class="btn">Connect Now</span>
</section>

<footer class="site-footer abs">
  <div class="f-box" style="left:145px;width:188px">Subscribe to Newsletter
    <div class="email-in"><div>Email here</div><b><svg width="8" height="11"><path d="M2 1l4 4.5L2 10" fill="none" stroke="#fff" stroke-width="2"/></svg></b></div>
  </div>
  <div class="f-box" style="left:374px;width:166px">Contact Us
    <small><svg width="9" height="9"><path d="M2 1c-2 2 1 6 5 7l1-2-2-1-1 1C4 5 3 4 3 3l1-1-1-1z" fill="#fff"/></svg>123 555 0190</small>
    <small><svg width="9" height="7"><rect x=".5" y=".5" width="8" height="6" fill="none" stroke="#fff"/><path d="M.5.5l4 3 4-3" fill="none" stroke="#fff"/></svg>support@velmorasystems.example.au</small>
  </div>
  <div class="f-box" style="left:581px;width:91px">Follow Us
    <div class="social"><i style="background:#3b5998"></i><i style="background:#29a9df"></i><i style="background:#f26522"></i></div>
  </div>
  <div class="f-brand abs"><i></i>Velmora Systems</div>
  <div class="f-links abs"><span class="on">Home</span> &nbsp;| &nbsp;About Us &nbsp;| &nbsp;Services | &nbsp;Support &nbsp;| &nbsp;Testimonials &nbsp;| &nbsp;Clients &nbsp;| &nbsp;Contact Us &nbsp;| &nbsp;Terms Conditions</div>
  <div class="copy abs">Copyright © 2014 &nbsp;velmorasystems. &nbsp;All Rights Reserved</div>
</footer>

</body>
</html>
```